Tusk Hollow Lodge website (design only)

Tusk Hollow Lodge (http://www.tuskhollowlodge-mw.example) is a private Safari lodge located in Malawi.
We would like a modern, professional website designed that does not subscribe to the cliched view of a Safari in Africa, but still maintain a wildlife/safari atmosphere.

The aim of our website is to entice people & drive them to the booking form.

Here are some examples of websites that we like. Although we would like our site to be a bit more in line with modern web design trends.

http://www.marulaplains.example/
http://www.kovunde.example/
http://www.tembalorecamp.example/

Requirements
Must have
• Here is a list of the pages required. Most of them will follow a standard content layout. I.e. heading, body and images.

If you take a look at the website, you will get an idea of hoe many page types there are +- 5

http://www.tuskhollowlodge-mw.example/index.htm

About Tusk Hollow
Lirundu Country Club
Rooms
Conferences
Cuisine
Facilities
Your Safari
Activities
Rates & Special Offers
Booking form
Latest Developments
How To Get There
Gallery
Contact Us
Blog / Newsfeed

```html
<!DOCTYPE html>
<html lang="en">
<head>
<meta charset="utf-8">
<title>Tusk Hollow Lodge</title>
<link rel="stylesheet" href="https://fonts.googleapis.com/css2?family=Arimo:wght@400;700&family=Cabin:wght@400;500&family=Great+Vibes&display=swap">
<style>
  :root {
    --bg: #2e2a27;
    --tan: #8c8266;
    --tan-dark: #766d54;
    --gold: #c9b27e;
    --cream: #d9d0b8;
    --body-text: #b9b3a8;
    --ink: #231f1c;
    --rule: #5a534a;
    --caption-bg: rgba(60, 52, 46, 0.72);
  }
  * { margin: 0; padding: 0; box-sizing: border-box; }
  html, body { width: 1200px; height: 900px; overflow: hidden; background: var(--bg); }
  body { position: relative; font-family: "Arimo", Arial, sans-serif; color: var(--body-text); }

  .brand { position: absolute; left: 52px; top: 28px; }
  .brand-name { font-family: "Cabin", sans-serif; font-weight: 400; font-size: 50px; color: var(--cream); letter-spacing: 1px; line-height: 1; }
  .brand-location { font-family: "Arimo", sans-serif; font-size: 13px; color: var(--cream); letter-spacing: 1px; margin: 8px 0 0 66px; }
  .tagline { position: absolute; right: 58px; top: 40px; font-family: "Great Vibes", cursive; font-size: 36px; color: var(--cream); opacity: .85; }

  .main-nav { position: absolute; left: 54px; top: 129px; width: 1096px; height: 32px;
    background: linear-gradient(#958b6f, var(--tan)); display: flex; align-items: center; padding: 0 8px; }
  .main-nav a { font-size: 14px; color: var(--ink); text-decoration: none; padding: 0 17px; border-right: 1px solid #6d6450; line-height: 14px; }
  .main-nav a:last-child { border-right: 0; }
  .main-nav a.current { padding: 0 17px; }

  .showcase { position: absolute; left: 54px; top: 161px; width: 1096px; height: 373px; background: var(--tan); padding: 0 7px 7px; display: flex; }
  .showcase-panel { position: relative; flex: 1; }
  .panel-image { position: absolute; inset: 0; }
  .lodge-img { background: linear-gradient(160deg, #caa86f 0%, #9b2a22 35%, #6a3a1e 65%, #7a2420 100%); }
  .safari-img { background: linear-gradient(180deg, #5d8fc2 0%, #9bb4c4 45%, #b69474 70%, #8a6a52 100%); }
  .plant-img { background: linear-gradient(135deg, #2f6a10 0%, #7fb52a 45%, #4a8a14 75%, #a6cf3c 100%); }
  .golf-img { background: linear-gradient(180deg, #dfe4e2 0%, #3c5a1a 30%, #6e9a2a 60%, #8fbd34 100%); }
  .panel-caption { position: absolute; left: 0; right: 0; top: 304px; height: 44px; background: var(--caption-bg);
    font-family: "Cabin", sans-serif; font-size: 18px; color: #fff; text-transform: uppercase; letter-spacing: .5px; padding: 14px 0 0 9px; }

  .feature { position: absolute; top: 553px; }
  .feature-title { font-family: "Cabin", sans-serif; font-weight: 500; font-size: 14.5px; color: var(--gold); text-transform: uppercase;
    text-align: center; border-top: 1px solid var(--rule); border-bottom: 1px solid var(--rule); padding: 12px 0 11px; }
  .feature-text { font-size: 13.3px; line-height: 19.7px; margin-top: 17px; }
  .feature-links { font-size: 13.3px; color: var(--gold); }
  .feature-links span { color: var(--body-text); margin: 0 8px; }
  .col-divider { position: absolute; top: 553px; width: 1px; height: 168px; background: #48423b; }

  .thumb { position: absolute; top: 751px; height: 90px; border: 2px solid var(--cream); }
  .thumb-building { background: linear-gradient(180deg, #b7c6cf 0%, #2f6a48 40%, #8a4a32 65%, #7a8a4a 100%); }
  .thumb-antelope { background: linear-gradient(180deg, #3b5a26 0%, #b0763e 50%, #e2c8a4 80%, #6a5a3a 100%); }
  .thumb-room { background: linear-gradient(160deg, #e0c69a 0%, #a8241e 40%, #6e3a1c 75%, #8a2a22 100%); }
  .thumb-conference { background: linear-gradient(180deg, #b8a580 0%, #f2ede4 40%, #8a1f30 70%, #eee8de 100%); }

  .site-footer { position: absolute; left: 0; top: 871px; width: 1200px; height: 29px; background: var(--tan);
    font-size: 12.5px; color: var(--ink); }
  .footer-icons { position: absolute; left: 50px; top: 0; height: 29px; display: flex; align-items: center; }
  .footer-icons .icon { width: 42px; display: flex; justify-content: center; border-right: 1px solid #6d6450; height: 29px; align-items: center; }
  .footer-icons .icon:first-child { border-left: 1px solid #6d6450; }
  .footer-text { position: absolute; left: 322px; top: 8px; }
  .footer-text span { margin: 0 6px; }
</style>
</head>
<body>
  <header>
    <div class="brand">
      <div class="brand-name">Tusk Hollow Lodge</div>
      <div class="brand-location">KALUNGWE ESTATE &nbsp;|&nbsp; NDAZI</div>
    </div>
    <div class="tagline">Experience the endless beauty of Nature</div>
  </header>

  <nav class="main-nav">
    <a href="#">Home</a><a href="#">About</a><a href="#" class="current">Gallery</a><a href="#">Safari</a><a href="#">Lodge</a><a href="#">Activities</a><a href="#">Rates &amp; Specials</a><a href="#">Bookings</a><a href="#">Developments</a><a href="#">Directions</a><a href="#">Blog</a><a href="#">Contact</a>
  </nav>

  <section class="showcase">
    <div class="showcase-panel">
      <div class="panel-image lodge-img" role="img" aria-label="Lodge lounge with red sofa, lamp and wooden table"></div>
      <div class="panel-caption">Tusk Hollow Lodge</div>
    </div>
    <div class="showcase-panel">
      <div class="panel-image safari-img" role="img" aria-label="Kudu antelope with spiral horns against blue sky"></div>
      <div class="panel-caption">On Safari</div>
    </div>
    <div class="showcase-panel">
      <div class="panel-image plant-img" role="img" aria-label="Close-up of green leaves"></div>
      <div class="panel-caption">Plant Life</div>
    </div>
    <div class="showcase-panel">
      <div class="panel-image golf-img" role="img" aria-label="Golf club and ball on green fairway"></div>
      <div class="panel-caption">Dam &amp; Golf Course</div>
    </div>
  </section>

  <article class="feature" style="left:56px;width:232px">
    <h2 class="feature-title">Tusk Hollow Lodge</h2>
    <p class="feature-text">Warmest welcome to the unique Malawi experience: lodge complex, game park, the 18 hole Lirundu golf club &amp; Kasonje dam. Tusk Hollow Lodge provides all the holiday and business prerequisites in a beautiful, relaxing environment.<br><span class="feature-links">Read more...</span></p>
  </article>
  <div class="col-divider" style="left:318px"></div>

  <article class="feature" style="left:350px;width:215px">
    <h2 class="feature-title">Game &amp; Wild Birds</h2>
    <p class="feature-text">Lorem ipsum dolor sit amet, consect etuer adipiscing elit, sed diam nonum my nibh euismod tincidunt ut laoreet dolore magna aliquam erat volutpat. Ut wisi enim ad minim veniam quis no strud exerci tatin ullamcorper suscipit<br><span class="feature-links">Read more<span>|</span>Booking Enquiry</span></p>
  </article>
  <div class="col-divider" style="left:597px"></div>

  <article class="feature" style="left:629px;width:220px">
    <h2 class="feature-title">The Lodge &amp; Rooms</h2>
    <p class="feature-text">Lorem ipsum dolor sit amet, consect etuer adipiscing elit, sed diam nonum my nibh euismod tincidunt ut laoreet dolore magna aliquam erat volutpat. Ut wisi enim ad minim veniam quis no strud exerci tatin ullamcorper suscipit<br><span class="feature-links">Read more<span>|</span>Booking Enquiry</span></p>
  </article>
  <div class="col-divider" style="left:884px"></div>

  <article class="feature" style="left:919px;width:215px">
    <h2 class="feature-title">Conference &amp; Resturant</h2>
    <p class="feature-text">Lorem ipsum dolor sit amet, consect etuer adipiscing elit, sed diam nonum my nibh euismod tincidunt ut laoreet dolore magna aliquam erat volutpat. Ut wisi enim ad minim veniam quis no strud exerci tatin ullamcorper suscipit<br><span class="feature-links">Read more<span>|</span>Booking Enquiry</span></p>
  </article>

  <div class="thumb thumb-building" style="left:54px;width:234px" role="img" aria-label="Lodge building with green roof and lawn"></div>
  <div class="thumb thumb-antelope" style="left:340px;width:234px" role="img" aria-label="Two young antelope in the bush"></div>
  <div class="thumb thumb-room" style="left:624px;width:234px" role="img" aria-label="Lodge room with red sofa and coffee table"></div>
  <div class="thumb thumb-conference" style="left:910px;width:236px" role="img" aria-label="Conference room set with tables"></div>

  <footer class="site-footer">
    <div class="footer-icons">
      <div class="icon" aria-label="Social link"><svg width="10" height="10"><circle cx="5" cy="5" r="4.5" fill="#5e5644"/></svg></div>
      <div class="icon" aria-label="Social link"><svg width="10" height="10"><circle cx="5" cy="5" r="4.5" fill="#5e5644"/></svg></div>
      <div class="icon" aria-label="Social link"><svg width="10" height="10"><circle cx="5" cy="5" r="4.5" fill="#5e5644"/></svg></div>
      <div class="icon" aria-label="Email"><svg width="14" height="10" viewBox="0 0 14 10"><rect x="0.5" y="0.5" width="13" height="9" fill="#5e5644"/><path d="M0.5 0.5 L7 5.5 L13.5 0.5" fill="none" stroke="#8c8266" stroke-width="1"/></svg></div>
    </div>
    <div class="footer-text">Tusk Hollow Lodge copyright &copy; 2012<span>|</span>Privacy Policy<span>|</span>Blog<span>|</span>Contact<span>|</span>Booking Enquiries</div>
  </footer>
</body>
</html>
```